New business card for a regional office of a US M&A company

We need business card for a finance company, office based in Hong Kong , our Head office is in US, our business is to Merge and acquires companies , the new office will be a regional office for the Asia Pacific region. We want to use the head office logo as attached ( but don't have to be exactly the same, can be a variation to it) as a base and then add Asia Pacific alongside the logo.
We would prefer to have be bilingual Eng + Chinese, although we don't really have Chinese company name .

Industry/Entity Type

Business

Contact Information for Business Card

Clara Jo Tsang
 

VP,
APAC M&A Operations
Orin Vantage Asia Pacific Limited
 
Unit 1407, K18
18 Tai Lok Shan Road, 
Hong Kong 
 
M: +852 6038 1742
T : +852 2836 4100
F : +852 2836 4177
VOIP: 4158
 
cjtsang@orinvantage.com

Font styles to use
Serif
Sans Serif

Colors

Designer to choose colors to be used in the design.

Requirements
Must have
• APAC Office

```html
<!DOCTYPE html>
<html lang="en">
<head>
<meta charset="utf-8">
<title>Orin Vantage – Business Card</title>
<link rel="stylesheet" href="https://fonts.googleapis.com/css2?family=Roboto:wght@400;500&family=Roboto+Condensed:wght@700&family=Source+Sans+3:wght@700&display=swap">
<style>
  :root {
    --stage: #e6e4e0;
    --navy: #0e2a45;
    --cyan: #1ea7d2;
    --ink-light: #e4e9ef;
    --mark-light: #eef1f4;
    --divider: #4d6580;
  }
  * { box-sizing: border-box; margin: 0; padding: 0; }
  html, body { width: 1200px; height: 960px; overflow: hidden; }
  body { background: var(--stage); position: relative; font-family: "Roboto", Arial, sans-serif; }

  .card {
    position: absolute;
    width: 600px;
    height: 343px;
    background: var(--navy);
    box-shadow: 0 2px 6px rgba(0,0,0,0.25);
  }
  .card--front { left: 314px; top: 113px; }
  .card--back { left: 311px; top: 472px; }

  /* front */
  .brand-mark {
    position: absolute;
    left: 153px; top: 128px;
    width: 36px; height: 36px;
    background: var(--mark-light);
  }
  .brand-name {
    position: absolute;
    left: 30px; top: 180px;
    width: 282px;
    text-align: center;
    font-family: "Source Sans 3", "Myriad Pro", sans-serif;
    font-weight: 700;
    font-size: 34px;
    letter-spacing: 0.5px;
    color: var(--cyan);
    white-space: nowrap;
  }
  .divider {
    position: absolute;
    left: 320px; top: 52px;
    width: 1px; height: 275px;
    background: linear-gradient(to bottom, transparent, var(--divider) 15%, var(--divider) 85%, transparent);
  }
  .contact { position: absolute; left: 348px; top: 58px; color: var(--ink-light); }
  .contact__name {
    font-family: "Roboto Condensed", "Arial Narrow", sans-serif;
    font-weight: 700;
    font-size: 22px;
    color: var(--cyan);
    text-transform: uppercase;
    line-height: 24px;
  }
  .contact__title { font-size: 15px; font-weight: 500; margin: 1px 0 0 2px; line-height: 20px; }
  .contact__address { font-size: 14.5px; line-height: 18.5px; margin-top: 8px; }
  .contact__lines { list-style: none; margin-top: 9px; font-size: 14.5px; line-height: 19px; }
  .contact__lines li { display: flex; align-items: center; }
  .contact__lines svg { width: 14px; height: 14px; margin-right: 9px; fill: var(--cyan); }
  .contact__voip { font-size: 14.5px; margin-top: 9px; }

  .edge-line {
    position: absolute; left: 0; right: 0; top: 324px;
    height: 2px; background: #ffffff;
  }
  .edge-band {
    position: absolute; left: 0; right: 0; bottom: 0;
    height: 15px; background: var(--cyan);
  }

  /* back */
  .back-mark {
    position: absolute;
    left: 276px; top: 98px;
    width: 48px; height: 48px;
    background: var(--mark-light);
  }
  .back-name {
    position: absolute;
    left: 0; right: 0; top: 164px;
    text-align: center;
    font-family: "Source Sans 3", "Myriad Pro", sans-serif;
    font-weight: 700;
    font-size: 30px;
    color: var(--mark-light);
  }
  .back-web {
    position: absolute;
    left: 0; right: 0; top: 284px;
    text-align: center;
    font-size: 14px;
    letter-spacing: 6.5px;
    color: var(--ink-light);
  }
</style>
</head>
<body>

<section class="card card--front">
  <div class="brand-mark"></div>
  <div class="brand-name">ORIN VANTAGE</div>
  <div class="divider"></div>

  <div class="contact">
    <h1 class="contact__name">Clara Jo Tsang</h1>
    <p class="contact__title">VP</p>
    <address class="contact__address" style="font-style:normal">
      APAC M&amp;A Operations<br>
      Orin Vantage Asia Pacific Limited<br>
      Unit 1407, K18<br>
      18 Tai Lok Shan Road<br>
      Hong Kong
    </address>
    <ul class="contact__lines">
      <li>
        <svg viewBox="0 0 16 16" aria-hidden="true"><path d="M3.5 1.5l2.3-.3 1.3 3.3-1.5 1.2c.8 1.7 2 2.9 3.7 3.7l1.2-1.5 3.3 1.3-.3 2.3c-.2 1-1 1.5-2 1.4C6.6 12.4 3.6 9.4 2.1 4.5 1.9 3.5 2.5 1.7 3.5 1.5z"/></svg>
        +852 2836 4100
      </li>
      <li>
        <svg viewBox="0 0 16 16" aria-hidden="true"><path d="M4.5 1h7a1 1 0 011 1v12a1 1 0 01-1 1h-7a1 1 0 01-1-1V2a1 1 0 011-1zm.8 2v9h5.4V3zM8 12.6a.8.8 0 100 1.6.8.8 0 000-1.6z" fill-rule="evenodd"/></svg>
        +852 6038 1742
      </li>
      <li>
        <svg viewBox="0 0 16 16" aria-hidden="true"><path d="M4 1h8v4H4zM1.5 6h13a1 1 0 011 1v5h-2.5v3h-10v-3H.5V7a1 1 0 011-1zm3 5v2.5h7V11z" fill-rule="evenodd"/></svg>
        +852 2836 4177
      </li>
    </ul>
    <p class="contact__voip">VOIP: 4158</p>
  </div>

  <div class="edge-line"></div>
  <div class="edge-band"></div>
</section>

<section class="card card--back">
  <div class="back-mark"></div>
  <div class="back-name">ORIN VANTAGE</div>
  <p class="back-web">www.orinvantage.com</p>
</section>

</body>
</html>
```